I need a business card to launch my business. I am a carpenter who works with wood and metal framing. I do commercial and residential properties. I do the final fixtures in expensive residential properties. For example custom made wardrobes, prefinished doors and skirtings. I have an eye for detail and take pride in my work.

I don't want to be pigeon holed as a guy with a tool belt and a hammer. I want to look like a professional company. I want my logo to be modern and young and edgy. I don't have any preference for colours but don't want yellow.

Industry/Entity Type

Residential

Contact Information for Business Card

Oakridge Joinery Co
specialising in residential and commercial fit outs

Mark Delaney
Phone: 0417 358 260
oakridgejoineryco@mailbox-example.net

Logo styles of interest
Pictorial/Combination Logo
Wordmark Logo
Lettermark Logo

```html
<!DOCTYPE html>
<html lang="en">
<head>
<meta charset="utf-8">
<title>Oakridge Joinery Co – Business Card</title>
<link rel="stylesheet" href="https://fonts.googleapis.com/css2?family=Roboto+Slab:wght@300;400&display=swap">
<style>
  :root {
    --bg: #2a2a2a;
    --card: #050505;
    --gold: #d6a93f;
    --silver: #d9d9d9;
    --muted: #bdbdbd;
  }
  * { margin: 0; padding: 0; box-sizing: border-box; }
  html, body { width: 1200px; height: 900px; overflow: hidden; }
  body {
    background: var(--bg);
    font-family: "Roboto Slab", Georgia, serif;
    display: flex;
    align-items: center;
    justify-content: center;
    gap: 60px;
  }
  .card {
    width: 520px;
    height: 318px;
    background: var(--card);
    position: relative;
    box-shadow: 0 18px 40px rgba(0,0,0,0.55);
  }
  .brand-name {
    font-weight: 400;
    color: var(--silver);
    letter-spacing: 0.06em;
    text-transform: uppercase;
    white-space: nowrap;
  }
  /* Front */
  .card-front {
    display: flex;
    flex-direction: column;
    align-items: center;
    justify-content: center;
  }
  .card-front .brand-name { font-size: 30px; margin-bottom: 28px; }
  .tagline {
    font-weight: 300;
    font-size: 15px;
    line-height: 1.35;
    color: var(--muted);
    text-align: center;
  }
  .tagline .accent { color: var(--gold); }
  /* Back */
  .card-back .brand-name {
    position: absolute;
    right: 40px;
    top: 108px;
    font-size: 18px;
  }
  .contact {
    position: absolute;
    right: 40px;
    top: 168px;
    text-align: right;
    font-weight: 300;
  }
  .contact-name {
    color: var(--gold);
    font-size: 19px;
    font-weight: 400;
    letter-spacing: 0.04em;
    text-transform: uppercase;
    margin-bottom: 4px;
  }
  .contact-line {
    font-size: 12.5px;
    color: var(--silver);
  }
  .contact-line .label, .contact-line .sep { color: var(--gold); }
</style>
</head>
<body>
  <section class="card card-front">
    <div class="brand-name">Oakridge Joinery Co</div>
    <p class="tagline">
      specialising in<br>
      <span class="accent">residential</span> and <span class="accent">commercial</span> fit outs
    </p>
  </section>

  <section class="card card-back">
    <div class="brand-name">Oakridge Joinery Co</div>
    <div class="contact">
      <div class="contact-name">Mark Delaney</div>
      <div class="contact-line">
        <span class="label">P:</span> 0417 358 260 <span class="sep">//</span>
        mark@oakridgejoinery.example
      </div>
    </div>
  </section>
</body>
</html>
```